Modern Business Card for Larkwell 2018

Our company assumes the best about people. We are creating an online community of entrepreneurs and business leaders who struggle with marketing their business online.

This business card should POP! We recently got a new logo and are launching a new website next month, so our business cards should make a statement that feels:
-Fresh
-Smart
-Trustworthy
-Fun

Target Market(s)

small business owners, entrepreneurs

Industry/Entity Type

Digital Marketing

Contact Information for Business Card

Dimensions: 3.5" x 2"

Font styles to use
Sans Serif

Colors
f37122
ffffff

Requirements
Must have
• We need a business card with a modern, bold design. We will use one side of the card as a lead-generation offer, so text on one side will need to fit up to 140 characters. The business card should stick to our core colors (orange, black, and white).
Nice to have
• We think a vertical "portrait" design could be interesting.
Should not have
• Should not look like a traditional business card. The round icon should stand out from a distance.

```html
<!DOCTYPE html>
<html lang="en">
<head>
<meta charset="utf-8">
<title>Larkwell Business Card</title>
<link href="https://fonts.googleapis.com/css2?family=Raleway:wght@400;600;700;800&family=Delius&display=swap" rel="stylesheet">
<style>
  :root {
    --orange: #f26b27;
    --orange-faint: #fde6da;
    --ink: #1f1f1f;
    --white: #ffffff;
    --backdrop: #3b3229;
  }
  * { margin: 0; padding: 0; box-sizing: border-box; }
  html, body { width: 1200px; height: 1200px; overflow: hidden; }
  body { background: var(--backdrop); position: relative; font-family: "Raleway", sans-serif; }

  .card {
    position: absolute; top: 218px; width: 412px; height: 718px;
    border-radius: 24px; overflow: hidden; background: var(--white);
  }
  .card--front { left: 168px; }
  .card--back { left: 622px; }

  /* Front */
  .front__top { position: absolute; left: 0; top: 0; width: 100%; height: 168px; background: var(--ink); }
  .front__badge {
    position: absolute; left: 134px; top: 96px; width: 144px; height: 144px;
    border-radius: 50%; background: var(--white);
  }
  .front__badge::after {
    content: ""; position: absolute; left: 12px; top: 12px; width: 120px; height: 120px;
    border-radius: 50%; background: var(--orange);
  }
  .brand-name {
    position: absolute; width: 100%; text-align: center;
    font-weight: 800; letter-spacing: 1px; line-height: 1;
  }
  .front__brand { top: 250px; font-size: 44px; color: var(--orange); }
  .tagline {
    position: absolute; width: 100%; text-align: center;
    font-family: "Delius", cursive; font-size: 19px; line-height: 1; letter-spacing: 0.5px;
  }
  .front__tagline { top: 295px; color: var(--ink); }

  .person__name {
    position: absolute; top: 481px; width: 100%; text-align: center;
    font-size: 31px; font-weight: 700; color: var(--ink); line-height: 1; letter-spacing: 0.5px;
  }
  .person__name .first { color: var(--orange); }
  .person__role {
    position: absolute; top: 515px; width: 100%; text-align: center;
    font-size: 17px; font-weight: 400; color: #333; line-height: 1;
  }
  .front__contact-band { position: absolute; left: 0; top: 570px; width: 100%; height: 148px; background: var(--orange); }
  .contact-icons { position: absolute; top: 554px; left: 0; width: 100%; height: 30px; }
  .contact-list {
    position: absolute; top: 600px; width: 100%; list-style: none; text-align: center;
    color: var(--white); font-size: 17px; letter-spacing: 1px; line-height: 25px;
  }

  /* Back */
  .back__top { position: absolute; left: 0; top: 0; width: 100%; height: 168px; background: var(--orange); }
  .back__brand { top: 50px; font-size: 50px; color: var(--white); }
  .back__tagline { top: 99px; color: var(--ink); }
  .back__mark {
    position: absolute; left: 98px; top: 297px; width: 212px; height: 212px;
    border-radius: 50%; background: var(--orange-faint);
  }
  .back__web {
    position: absolute; left: 80px; top: 630px; width: 252px; height: 33px;
    border-top: 1.5px solid var(--ink); border-bottom: 1.5px solid var(--ink);
    text-align: center; font-size: 16px; letter-spacing: 2.5px; line-height: 30px; color: var(--ink);
  }
  .back__web .accent { color: var(--orange); }
  .back__bottom { position: absolute; left: 0; bottom: 0; width: 100%; height: 24px; background: var(--ink); }
</style>
</head>
<body>

<section class="card card--front" aria-label="Business card front">
  <div class="front__top"></div>
  <div class="front__badge"></div>
  <div class="brand-name front__brand">LARKWELL</div>
  <div class="tagline front__tagline">Share ideas that spark progress</div>

  <div class="person__name"><span class="first">DANA</span> MORROW</div>
  <div class="person__role">Story Marketing Coach</div>

  <div class="front__contact-band"></div>
  <svg class="contact-icons" viewBox="0 0 412 30" aria-hidden="true">
    <g transform="translate(154 15)">
      <circle r="15" fill="#ffffff"/><circle r="12.5" fill="#1f1f1f"/>
      <path d="M-5 -6 l3 -1 l2 4 l-2 1.5 q1.5 3.5 4.5 4.5 l1.5 -2 l4 2 l-1 3 q-8 1 -12 -12z" fill="#fff"/>
    </g>
    <g transform="translate(205 15)">
      <circle r="15" fill="#ffffff"/><circle r="12.5" fill="#1f1f1f"/>
      <path d="M-7 0 L7 -6 L3 7 L0 2 Z" fill="#fff"/>
    </g>
    <g transform="translate(258 15)">
      <circle r="15" fill="#ffffff"/><circle r="12.5" fill="#1f1f1f"/>
      <path d="M-5 -6 L6 -1 L1 0 L4 5 L2 6 L-1 1 L-4 4 Z" fill="#fff"/>
    </g>
  </svg>
  <ul class="contact-list">
    <li>000-000-0000</li>
    <li>dana@larkwellhub.com</li>
    <li>www.larkwellhub.com</li>
  </ul>
</section>

<section class="card card--back" aria-label="Business card back">
  <div class="back__top"></div>
  <div class="brand-name back__brand">LARKWELL</div>
  <div class="tagline back__tagline">Share ideas that spark progress</div>
  <div class="back__mark"></div>
  <div class="back__web">www.<span class="accent">larkwellhub</span>.com</div>
  <div class="back__bottom"></div>
</section>

</body>
</html>
```